holloway paving service

Needs to have phone number 0418259730 and email markholloway@brightmail.com.au.
ABN 62318470915
name mark holloway

For all your concreting solutions
Excavation
Exposed & colour concrete
House & shed slabs
Driveways
Landing & steps

Contact Information for Business Card

ph 0418259730
email markholloway@brightmail.com.au.
ABN 62318470915
name mark holloway

```html
<!DOCTYPE html>
<html lang="en">
<head>
<meta charset="utf-8">
<title>Holloway Paving Service – Business Card</title>
<link rel="stylesheet" href="https://fonts.googleapis.com/css2?family=Montserrat:wght@500;600&family=Open+Sans:wght@400;600&display=swap">
<style>
  :root {
    --backdrop: #9a9a9a;
    --card-light: #ffffff;
    --card-dark: #0b0a0a;
    --orange: #f26d21;
    --grey: #6d6e70;
    --ink: #1e1e1e;
    --rule: #8a8a8a;
    --white: #ffffff;
  }
  * { margin: 0; padding: 0; box-sizing: border-box; }
  html, body { width: 1200px; height: 900px; overflow: hidden; }
  body {
    position: relative;
    background: var(--backdrop);
    font-family: "Open Sans", Arial, sans-serif;
  }
  .card {
    position: absolute;
    width: 477px;
    height: 294px;
    box-shadow: 2px 3px 6px rgba(0,0,0,0.35);
  }
  .card--front {
    left: 121px; top: 275px;
    background: var(--card-light);
    border-radius: 0 46px 0 46px;
  }
  .card--back {
    left: 606px; top: 274px;
    background: var(--card-dark);
    border-radius: 46px 0 46px 0;
  }
  .brand__mark {
    position: absolute;
    width: 40px; height: 40px;
    background: var(--orange);
  }
  .brand__name {
    position: absolute;
    font-family: "Montserrat", Arial, sans-serif;
    font-weight: 600;
    font-size: 18px;
    line-height: 23px;
    letter-spacing: 0.2px;
    color: var(--orange);
    text-transform: uppercase;
  }
  .card--front .brand__mark { left: 158px; top: 87px; }
  .card--front .brand__name { left: 237px; top: 81px; }
  .card--back .brand__mark { left: 144px; top: 84px; }
  .card--back .brand__name { left: 224px; top: 78px; }
  .holder {
    position: absolute;
    left: 25px; top: 187px;
    font-family: "Montserrat", Arial, sans-serif;
    font-weight: 600;
    font-size: 17px;
    color: var(--grey);
    text-transform: uppercase;
  }
  .holder__first { color: var(--orange); }
  .holder-rule {
    position: absolute;
    left: 25px; top: 214px;
    width: 429px; height: 1px;
    background: var(--rule);
  }
  .contact {
    position: absolute;
    left: 25px; top: 228px;
    list-style: none;
    font-size: 13px;
    line-height: 18px;
    color: var(--ink);
  }
  .contact li { display: flex; align-items: center; gap: 5px; }
  .contact svg { width: 11px; height: 11px; fill: var(--orange); }
  .abn {
    position: absolute;
    right: 23px; top: 246px;
    font-size: 13px;
    line-height: 18px;
    color: var(--ink);
  }
  .tagline {
    position: absolute;
    left: 37px; top: 193px;
    width: 403px;
    display: flex;
    align-items: center;
    gap: 8px;
    font-size: 11px;
    color: var(--orange);
    text-transform: uppercase;
  }
  .tagline::after {
    content: "";
    flex: 1;
    height: 1px;
    background: var(--grey);
  }
  .services {
    position: absolute;
    list-style: none;
    font-size: 13px;
    line-height: 17.5px;
    color: var(--white);
  }
  .services--main { left: 38px; top: 218px; }
  .services--extra { left: 287px; top: 224px; }
  .services li { display: flex; align-items: center; gap: 8px; }
  .services li::before {
    content: "";
    width: 6px; height: 6px;
    border-radius: 50%;
    background: var(--orange);
  }
</style>
</head>
<body>
  <section class="card card--front">
    <span class="brand__mark"></span>
    <span class="brand__name">Holloway Paving<br>Service</span>
    <p class="holder"><span class="holder__first">Mark</span> Holloway</p>
    <div class="holder-rule"></div>
    <ul class="contact">
      <li>
        <svg viewBox="0 0 24 24" aria-hidden="true"><path d="M6.6 10.8a15.1 15.1 0 0 0 6.6 6.6l2.2-2.2c.3-.3.7-.4 1-.2 1.1.4 2.3.6 3.6.6.6 0 1 .4 1 1V20c0 .6-.4 1-1 1A17 17 0 0 1 3 4c0-.6.4-1 1-1h3.5c.6 0 1 .4 1 1 0 1.3.2 2.5.6 3.6.1.3 0 .7-.2 1z"/></svg>
        0418259730
      </li>
      <li>
        <svg viewBox="0 0 24 24" aria-hidden="true"><path d="M2 5h20v14H2z"/><path d="M3 6l9 7 9-7" fill="none" stroke="#fff" stroke-width="2"/></svg>
        markholloway@brightmail.com.au
      </li>
    </ul>
    <p class="abn">ABN 62318470915</p>
  </section>

  <section class="card card--back">
    <span class="brand__mark"></span>
    <span class="brand__name">Holloway Paving<br>Service</span>
    <p class="tagline">For all your concreting solutions</p>
    <ul class="services services--main">
      <li>Excavation</li>
      <li>Exposed &amp; colour concrete</li>
      <li>House &amp; shed slabs</li>
    </ul>
    <ul class="services services--extra">
      <li>Driveways</li>
      <li>Landing &amp; steps</li>
    </ul>
  </section>
</body>
</html>
```